Awesome Digital Ad Design – Vexora Adloop

I am going to be setting up a Vexora Adloop ad campaign I need creatives for.

Several sizes are needed in the end, however, please submit your design concept in the following 2 sizes to start:
Medium rectangle: 300X250
Leaderboard: 728X90

Original artwork/design files and images used expected upon payment and as part of the final delivery.

Ads should match our company brand and the information on this webpage: http://www.harbelstandwork.com/real-estate-marketing/
SEE MORE INSTRUCTIONS IN ATTACHED WORD DOC

Target Market(s)

Business-To-Business Audience –Real Estate Company Executives (Presidents/VPs/Owners/CEOs/Sales Managers).

Industry/Entity Type

Real Estate

Font styles to use
Sans Serif

Requirements
Must have
• Copy should be minimal words, billboard like. Please use real photos/images that would appeal to real estate high-level decision-maker executives.
Should not have
• No cartoons or graphics

```html
<!DOCTYPE html>
<html lang="en">
<head>
<meta charset="utf-8">
<title>Harbel Standwork – Vexora Adloop Ad Concepts</title>
<link rel="stylesheet" href="https://fonts.googleapis.com/css2?family=Bebas+Neue&family=Oswald:wght@400&family=Roboto+Condensed:wght@700&display=swap">
<style>
  :root {
    --board: #2d2d2d;
    --maroon: #6e2a3a;
    --maroon-dark: #5c1f2f;
    --steel: #4f7896;
    --orange: #ef6a22;
    --orange-dark: #d9561a;
    --gold: #c9b57f;
    --white: #ffffff;
    --ink: #3a3a3a;
  }
  * { box-sizing: border-box; margin: 0; padding: 0; }
  html, body { width: 1200px; height: 1200px; overflow: hidden; background: var(--board); }
  .board { position: relative; width: 1200px; height: 1200px; }

  /* Medium rectangle */
  .ad-rect {
    position: absolute; left: 208px; top: 98px; width: 787px; height: 656px;
    overflow: hidden; font-family: "Bebas Neue", "Oswald", sans-serif;
  }
  .ad-rect .photo {
    position: absolute; inset: 0;
    background: linear-gradient(180deg, #c9d3dc 0%, #e4e8ea 35%, #a9b59b 72%, #d9ddd6 100%);
  }
  .ad-rect .person {
    position: absolute; right: 0; top: 0; width: 387px; height: 590px;
    background: linear-gradient(180deg, #c9a892 0%, #7a5a4e 30%, #5b4248 60%, #4c3840 100%);
    border-radius: 180px 0 0 0;
  }
  .ad-rect .brand-box {
    position: absolute; left: 36px; top: 0; width: 164px; height: 157px;
    background: var(--white); display: flex; align-items: center; justify-content: center;
  }
  .brand-name {
    font-family: "Oswald", sans-serif; font-weight: 400; color: var(--ink);
    text-align: center; line-height: 1.15; white-space: nowrap;
  }
  .ad-rect .brand-name { font-size: 22px; }
  .band {
    position: absolute; left: 0; color: var(--white); text-transform: uppercase;
    padding-left: 37px; white-space: nowrap;
  }
  .band-headline { top: 200px; width: 482px; height: 138px; background: var(--maroon); padding-top: 16px; }
  .band-headline .line-1 { font-size: 54px; line-height: 0.95; }
  .band-headline .line-2 { font-size: 74px; line-height: 0.95; }
  .band-offer { top: 354px; width: 408px; height: 118px; background: var(--steel); padding-top: 14px; }
  .band-offer .line-1 { font-size: 46px; line-height: 0.95; }
  .band-offer .line-2 { font-size: 64px; line-height: 0.95; }

  .cta {
    position: absolute; display: flex; align-items: center; justify-content: space-between;
    background: linear-gradient(180deg, var(--orange) 0%, var(--orange-dark) 100%);
    border: 2px solid #f7a06a; color: var(--white); text-transform: uppercase;
    white-space: nowrap;
  }
  .ad-rect .cta {
    left: 64px; top: 552px; width: 654px; height: 80px; border-radius: 10px;
    padding: 0 14px 0 18px; font-size: 54px; line-height: 1;
  }
  .ad-rect .cta span { padding-top: 4px; }
  .cta svg { flex: none; }

  /* Leaderboard */
  .ad-board {
    position: absolute; left: 48px; top: 915px; width: 1104px; height: 137px;
    overflow: hidden; background: linear-gradient(180deg, var(--maroon) 0%, var(--maroon-dark) 100%);
    font-family: "Roboto Condensed", sans-serif;
  }
  .ad-board .headline { position: absolute; left: 56px; top: 22px; text-transform: uppercase; white-space: nowrap; }
  .ad-board .headline .line-1 { color: var(--white); font-size: 40px; font-weight: 700; line-height: 1; }
  .ad-board .headline .line-2 { color: var(--gold); font-size: 54px; font-weight: 700; line-height: 1.02; }
  .ad-board .brand-circle {
    position: absolute; left: 440px; top: -8px; width: 152px; height: 152px;
    border-radius: 50%; background: var(--white);
    display: flex; align-items: center; justify-content: center;
  }
  .ad-board .brand-name { font-size: 21px; }
  .ad-board .offer {
    position: absolute; left: 620px; width: 274px; top: 24px; text-align: center;
    text-transform: uppercase; font-size: 26px; font-weight: 700; line-height: 1.02; white-space: nowrap;
  }
  .ad-board .offer .line-1 { color: var(--white); }
  .ad-board .offer .line-2 { color: var(--gold); }
  .ad-board .cta {
    left: 678px; top: 87px; width: 178px; height: 33px; border-radius: 4px;
    padding: 0 6px; font-size: 16px; font-weight: 700; line-height: 1;
  }
  .ad-board .photo {
    position: absolute; right: 0; top: 0; width: 170px; height: 137px;
    background: linear-gradient(180deg, #c7cfd6 0%, #8a6a62 45%, #4f3a42 100%);
  }
  .ad-board .chevron { position: absolute; left: 910px; top: 0; }
</style>
</head>
<body>
<main class="board">

  <section class="ad-rect" aria-label="Medium rectangle ad">
    <div class="photo" role="img" aria-label="Photo of a suburban house front with lawn, softly blurred"></div>
    <div class="person" role="img" aria-label="Photo of a smiling real estate agent in a plum blazer holding a SOLD sign"></div>
    <div class="brand-box"><span class="brand-name">Harbel<br>Standwork</span></div>
    <div class="band band-headline">
      <div class="line-1">Client Follow-Up</div>
      <div class="line-2">Made Simple</div>
    </div>
    <div class="band band-offer">
      <div class="line-1">Virtually No Cost To</div>
      <div class="line-2">Your Company!</div>
    </div>
    <a class="cta">
      <svg width="52" height="52" viewBox="0 0 24 24" aria-hidden="true">
        <path fill="#fff" d="M6.6 10.8c1.4 2.8 3.8 5.1 6.6 6.6l2.2-2.2c.3-.3.7-.4 1-.2 1.1.4 2.3.6 3.6.6.6 0 1 .4 1 1V20c0 .6-.4 1-1 1C10.6 21 3 13.4 3 4c0-.6.4-1 1-1h3.5c.6 0 1 .4 1 1 0 1.3.2 2.5.6 3.6.1.3 0 .7-.2 1z"/>
        <path fill="none" stroke="#fff" stroke-width="1.5" stroke-linecap="round" d="M14 7.5a3 3 0 0 1 2.5 2.5M14 4.5a6 6 0 0 1 5.5 5.5"/>
      </svg>
      <span>Call to Action: Learn More</span>
      <svg width="58" height="58" viewBox="0 0 40 40" aria-hidden="true">
        <circle cx="20" cy="20" r="18" fill="#fff"/>
        <path fill="var(--orange)" d="M11 16h9v-6l10 10-10 10v-6h-9z"/>
      </svg>
    </a>
  </section>

  <section class="ad-board" aria-label="Leaderboard ad">
    <div class="headline">
      <div class="line-1">Client Follow-Up</div>
      <div class="line-2">Made Simple</div>
    </div>
    <div class="brand-circle"><span class="brand-name">Harbel<br>Standwork</span></div>
    <div class="offer">
      <div class="line-1">Virtually No Cost To</div>
      <div class="line-2">Your Company!</div>
    </div>
    <a class="cta">
      <svg width="20" height="20" viewBox="0 0 24 24" aria-hidden="true">
        <path fill="#fff" d="M6.6 10.8c1.4 2.8 3.8 5.1 6.6 6.6l2.2-2.2c.3-.3.7-.4 1-.2 1.1.4 2.3.6 3.6.6.6 0 1 .4 1 1V20c0 .6-.4 1-1 1C10.6 21 3 13.4 3 4c0-.6.4-1 1-1h3.5c.6 0 1 .4 1 1 0 1.3.2 2.5.6 3.6.1.3 0 .7-.2 1z"/>
      </svg>
      <span>Call to Action</span>
      <svg width="22" height="22" viewBox="0 0 40 40" aria-hidden="true">
        <circle cx="20" cy="20" r="18" fill="#fff"/>
        <path fill="var(--orange)" d="M11 16h9v-6l10 10-10 10v-6h-9z"/>
      </svg>
    </a>
    <div class="photo" role="img" aria-label="Photo of a smiling real estate agent holding a SOLD sign in front of a house"></div>
    <svg class="chevron" width="50" height="137" viewBox="0 0 50 137" aria-hidden="true">
      <path d="M0 0 L14 0 L46 68.5 L14 137 L0 137 L32 68.5 Z" fill="var(--maroon)"/>
      <path d="M14 0 L46 68.5 L14 137" fill="none" stroke="var(--gold)" stroke-width="4"/>
      <path d="M0 0 L32 68.5 L0 137" fill="none" stroke="var(--white)" stroke-width="3"/>
    </svg>
  </section>

</main>
</body>
</html>
```